new branding The Velvet Pour

The Velvet Pour is a Belgian brand of ready to serve mocktails. We're looking for a rebranding of the labels on our bottles (8 different flavours)
Our mocktails are low in sugar, 100% natural and completely alcohol-free. They are also 'ready to serve': gently shake the bottle, serve with ice cubes, finish and your mocktail is ready in no time!
Besides being the ideal aperitif, you can also serve them during brunch or dinner. Thanks to the different flavors, you can pair each mocktail with a dish.
Please visit our website to see the current look&feel: the velvetpour.com - https://thevelvetpour.lumagallery.com/

Target Market(s)

people looking for a premium alcoholfree alternative - premium market

Industry/Entity Type

Mocktails (our mocktails have unique flavors, it's not the non-alcoholic version of a cocktail)

Colors

Designer to choose colors to be used in the design.

Requirements
Must have
• Our brand should be more visible, more recognizable, bolder, without losing the premium and refined character. Base colors should be white, black and silver. The brand should be put more foward. Keep number concept (every mocktail has its number) Put the ingredients/flavours/combinations a bit more forward. make the brand more confident and mature. The eight bottles should become a family. PREMIUM EXPRESSION
Nice to have
• We want to work with a white label. Ideas for the shape of the label Some ideas for the label: Play with shapes, cut outs, texture and number of labels. We like the frosted look and the combination of print & label . Working with 2 labels gives it more dynamic, not one big block Clean label. Working with a cut out shape, can be the logo or the numbers ? Working with 2 labels makes it easier to create an importance of messages. Working with an organic shape makes it unique and give a natural touch Working with a cut out can give a color pop on the white label The label can have parts coming out of the square shape
Should not have
• No crazy stuff, finishes etc should be feasible/realistic

```html
<!DOCTYPE html>
<html lang="en">
<head>
<meta charset="utf-8">
<title>The Velvet Pour – Basil &amp; Elderflower N.1 label</title>
<link rel="stylesheet" href="https://fonts.googleapis.com/css2?family=Anton&family=Oswald:wght@300;400;500&family=Yellowtail&display=swap">
<style>
  :root {
    --canvas: #e4e4e4;
    --label: #ffffff;
    --ink: #1b1b1b;
    --rule: #555555;
    --engraving-light: #f4f4f4;
    --engraving-dark: #e2e2e2;
  }
  html, body {
    margin: 0;
    width: 1200px;
    height: 1200px;
    overflow: hidden;
    background: var(--canvas);
  }
  .stage {
    width: 1200px;
    height: 1200px;
    display: flex;
    align-items: center;
    justify-content: center;
  }
  .label { width: 560px; height: 1034px; display: block; }
  .label-body { fill: var(--label); stroke: var(--ink); stroke-width: 9; }
  .label-stitch { fill: none; stroke: var(--ink); stroke-width: 2.4; stroke-dasharray: 2 2.6; }
  .rule { stroke: var(--rule); stroke-width: 1.2; }
  .claim { font-family: "Oswald", sans-serif; font-weight: 400; font-size: 14px; letter-spacing: 1.6px; fill: var(--ink); }
  .brand-name { font-family: "Anton", sans-serif; fill: var(--ink); text-anchor: middle; letter-spacing: 1px; }
  .flavour { font-family: "Oswald", sans-serif; font-weight: 500; font-size: 44px; fill: var(--ink); letter-spacing: -0.5px; }
  .number { font-family: "Anton", sans-serif; font-size: 86px; fill: var(--ink); }
  .info { font-family: "Oswald", sans-serif; font-weight: 300; font-size: 15px; fill: var(--ink); letter-spacing: 0.8px; }
  .tagline { font-family: "Yellowtail", cursive; font-size: 22px; fill: var(--ink); }
  .serve-stamp-text { font-family: "Oswald", sans-serif; font-weight: 300; font-size: 9.5px; letter-spacing: 1px; fill: #777; }
  .serve-stamp-ring { fill: none; stroke: #888; stroke-width: 1.2; }
</style>
</head>
<body>
<main class="stage">
  <svg class="label" viewBox="0 0 456 842" xmlns="http://www.w3.org/2000/svg">
    <defs>
      <linearGradient id="engraving-tone" x1="0" y1="0" x2="1" y2="1">
        <stop offset="0" stop-color="var(--engraving-light)"/>
        <stop offset="1" stop-color="var(--engraving-dark)"/>
      </linearGradient>
      <path id="claim-arc" d="M 78 88 Q 228 18 378 88"/>
      <path id="stamp-circle" d="M 283 530 a 40 40 0 1 1 -0.1 0"/>
    </defs>

    <!-- label shape -->
    <path class="label-body" d="M 5 838 L 5 64 Q 228 -40 451 64 L 451 838 Z"/>
    <path class="label-stitch" d="M 19 824 L 19 74 Q 228 -20 437 74 L 437 824 Z"/>

    <!-- top claim -->
    <text class="claim"><textPath href="#claim-arc" startOffset="50%" text-anchor="middle">PREMIUM NON-ALCOHOLIC DRINK</textPath></text>

    <!-- engraving area behind brand name -->
    <rect x="30" y="195" width="380" height="285" rx="60" fill="url(#engraving-tone)" opacity="0.6"
          role="img" aria-label="Engraved lemon with leaves illustration"/>

    <!-- brand name -->
    <text class="brand-name" x="228" y="250" font-size="40">THE</text>
    <text class="brand-name" x="228" y="350" font-size="96">VELVET</text>
    <text class="brand-name" x="228" y="450" font-size="96">POUR</text>

    <!-- serving stamp -->
    <circle class="serve-stamp-ring" cx="283" cy="570" r="22"/>
    <text class="serve-stamp-text"><textPath href="#stamp-circle">GENTLY SHAKE THE BOTTLE · SERVE WITH ICE CUBES ·</textPath></text>

    <!-- flavour block -->
    <line class="rule" x1="38" y1="585" x2="412" y2="585"/>
    <text class="flavour" x="54" y="642">BASIL &amp;</text>
    <text class="flavour" x="54" y="694">ELDERFLOWER</text>
    <line class="rule" x1="290" y1="607" x2="290" y2="702"/>
    <text class="number" x="314" y="694">N.1</text>
    <line class="rule" x1="38" y1="722" x2="412" y2="722"/>

    <!-- serving line -->
    <text class="info" x="38" y="754">READY TO SERVE</text>
    <line class="rule" x1="182" y1="734" x2="182" y2="770"/>
    <text class="tagline" x="212" y="756">Fresh fruits &amp; herbs</text>
    <line class="rule" x1="38" y1="778" x2="412" y2="778"/>

    <!-- facts line -->
    <text class="info" x="38" y="808" textLength="374" lengthAdjust="spacing">100% NATURAL  |  ALCOHOL FREE  |  MADE IN BELGIUM</text>
  </svg>
</main>
</body>
</html>
```